Create an awesome website for a medical clinic

This is a new website for a doctor's office. The site should be clean and modern, easy to navigate.

This is a wellness clinic, we want to help our clients have a healthy, active lifestyle. It should be friendly and inviting, and easy for them to call or schedule an appointment.

The site should be responsive and designed using the attached Bootstrap 3 PSD.

We will provide stock photos, until then please use stock photos from:

pixelharbor.com or
framequarry.com (preferred)

Some example sites of clean and modern designs that we like:

https://tulsaspinecare.com/
http://reachpastjoints.com/
http://turninghealthier.com/

Also attached is a temporary logo you can use.

Reason: Thank you everyone for your great designs - we need a little more time so I'm extending the project.

Need extra days to review

Also, the colors in the new logo I just linked to are the final colors of the logo, so feel free to use any complimentary colors to it.

Hi everyone, The boss wants to change the layout of the site a little bit - here's the revised layout: https://www.filecrate.com/s/k9rt31vx2qp84zn/notes%2011_29_2017.pdf?dl=0 And the graphic assets you can use are here: https://www.filecrate.com/s/k9rt31vx2qp84zn/notes%2011_29_2017.pdf?dl=0 Feel free to change the background color of the "topbar", and change the icons of the "why people trust us" if you want, these are just temporary placeholders. Thanks for your patience and hard work!

Target Market(s)

People seeking medical treatment (wellness clinic)

Industry/Entity Type

Doctor

Number of Pages Required

1 page

Font styles to use
Sans Serif

Colors
0592cd
33a6d7
abd037
9bcb3c

Requirements
Must have
• The home page should have: a strong hero image/slideshow, clinic phone number should be prominent and at the top of the page (in the nav), a "what to expect" section (this is like a FAQs section - see attachment), and a strong call to action (a button to call or schedule an appointment).
• The what to expect section is useful so that prospective clients can determine if we're a good fit for them or not. It's a basic, first-step pre-qualification block of information.
• Social media icons which links to our social media profiles should be included.
Nice to have
• - Link to 3 most recent blog entries
• - Testimonials
• - How a multilevel nav menu looks.

```html
<!DOCTYPE html>
<html lang="en">
<head>
<meta charset="utf-8">
<title>Fernway Medical Clinic</title>
<link rel="stylesheet" href="https://fonts.googleapis.com/css2?family=Lato:wght@300;400;700&display=swap">
<style>
:root{
  --green:#9bcb3c;
  --lime:#abd037;
  --green-dark:#86b52c;
  --footer-bar:#8fbf2f;
  --blue:#0592cd;
  --blue-light:#33a6d7;
  --ink:#1e2a33;
  --muted:#6f7b84;
  --line:#dfe5ea;
  --white:#ffffff;
}
*{margin:0;padding:0;box-sizing:border-box}
html,body{width:1200px;height:3462px;overflow:hidden}
body{font-family:"Lato",Arial,sans-serif;color:var(--ink);background:var(--white);position:relative}
a{color:inherit;text-decoration:none}

/* Header */
.site-header{position:absolute;top:0;left:0;width:1200px;height:83px;background:var(--white);z-index:5;display:flex;align-items:center;padding:0 120px;white-space:nowrap}
.brand{display:flex;flex-direction:column;line-height:1}
.brand-name{font-size:36px;font-weight:700;color:var(--green-dark);letter-spacing:.5px}
.brand-sub{font-size:16px;font-weight:700;color:var(--green-dark);margin-top:3px}
.main-nav{display:flex;gap:30px;margin-left:56px;font-size:16px;color:#7d868d}
.main-nav a{white-space:nowrap}
.main-nav .active{color:var(--green);position:relative}
.main-nav .active::after{content:"";position:absolute;left:50%;bottom:-31px;margin-left:-9px;border:9px solid transparent;border-bottom-color:var(--green)}
.nav-phone{margin-left:auto;display:flex;align-items:center;gap:8px;font-size:20px;font-weight:700;color:var(--ink);white-space:nowrap}

/* Mega menu */
.mega-menu{position:absolute;top:83px;left:0;width:1200px;height:262px;background:var(--green);z-index:4;display:flex;padding:44px 0 0 127px}
.mega-col{width:235px}
.mega-col h4{font-size:15px;font-weight:700;color:var(--white);margin-bottom:10px;text-transform:uppercase}
.mega-col li{list-style:none;font-size:12px;font-weight:700;color:var(--white);line-height:23px}

/* Hero */
.hero{position:absolute;top:83px;left:0;width:1200px;height:540px;overflow:hidden}
.hero-photo{position:absolute;inset:0;background:linear-gradient(100deg,#c9d6c0 0%,#eef0ea 25%,#5e8a3a 55%,#7fae3f 80%,#4f7a2e 100%)}
.hero-title{position:absolute;top:226px;width:100%;text-align:center;color:var(--white);font-size:46px;font-weight:700;letter-spacing:2px}
.btn-ghost{position:absolute;top:298px;left:438px;width:324px;height:50px;border:2px solid var(--white);color:var(--white);font-size:20px;display:flex;align-items:center;justify-content:center;background:rgba(255,255,255,.12)}
.slider-dots{position:absolute;top:504px;left:0;width:100%;display:flex;justify-content:center;gap:8px}
.slider-dots span{width:13px;height:13px;border-radius:50%;border:2px solid var(--white)}
.slider-dots span.on{background:var(--white)}

/* Welcome */
.welcome{position:absolute;top:623px;left:0;width:1200px;height:477px;overflow:hidden}
.welcome svg{position:absolute;inset:0}
.welcome-copy{position:absolute;left:128px;top:76px;width:490px}
.welcome-copy h2{font-size:31px;font-weight:400;margin-bottom:22px;white-space:nowrap}
.lead{font-size:16px;color:var(--muted);line-height:24px;margin-bottom:18px}
.body-text{font-size:14px;color:var(--muted);line-height:23px}
.btn-solid{display:inline-flex;align-items:center;justify-content:center;width:174px;height:46px;margin-top:28px;background:linear-gradient(var(--blue-light),var(--blue));color:var(--white);font-weight:700;font-size:16px;border-radius:2px}

/* What to Expect */
.expect{position:absolute;top:1100px;left:0;width:1200px;height:580px;background:linear-gradient(110deg,var(--blue) 0%,#2a9fd0 45%,#7fc24a 85%,var(--lime) 100%)}
.expect h2{position:absolute;top:46px;width:100%;text-align:center;color:var(--white);font-size:33px;font-weight:400}
.accordion{position:absolute;top:123px;left:210px;width:792px}
.acc-open-head{height:47px;background:var(--white);color:var(--blue);font-weight:700;font-size:16px;display:flex;align-items:center;justify-content:space-between;padding:0 20px 0 26px}
.acc-body{height:126px;background:rgba(10,70,110,.35);color:var(--white);font-size:14px;line-height:25px;padding:20px 30px 0 30px}
.acc-item{height:45px;margin-top:5px;border:2px solid rgba(255,255,255,.85);color:var(--white);font-weight:700;font-size:15px;display:flex;align-items:center;justify-content:space-between;padding:0 20px 0 26px}
.acc-item:first-of-type{margin-top:4px}

/* Blogs */
.blogs{position:absolute;top:1680px;left:0;width:1200px;height:470px}
.blogs h2{position:absolute;left:125px;top:46px;font-size:33px;font-weight:400}
.blog-card{position:absolute;top:116px;width:300px;height:344px;border:1px solid var(--line);background:var(--white)}
.blog-photo{height:195px;background:linear-gradient(160deg,#d8e2e8,#9fb0bd)}
.blog-card:nth-of-type(2) .blog-photo{background:linear-gradient(160deg,#7da545,#c7d9a3)}
.blog-card:nth-of-type(3) .blog-photo{background:linear-gradient(160deg,#eef1f4,#b9c6cf)}
.blog-date{position:absolute;left:-8px;top:143px;width:66px;height:60px;background:var(--green);color:var(--white);text-align:center;padding-top:4px}
.blog-date b{display:block;font-size:28px;font-weight:400;line-height:30px}
.blog-date small{font-size:14px}
.blog-text{padding:16px 24px 0 24px}
.blog-text h3{font-size:18px;font-weight:400;margin-bottom:10px}
.blog-text p{font-size:11px;color:var(--muted);line-height:16px}
.read-more{display:block;margin-top:12px;font-size:11px;font-weight:700;color:var(--blue)}

/* Testimonials */
.testimonials{position:absolute;top:2140px;left:0;width:1200px;height:480px;background:linear-gradient(180deg,var(--blue) 0%,#1a8fc6 100%);overflow:hidden}
.testimonials .wave{position:absolute;top:0;left:0}
.testimonials h2{position:absolute;top:138px;width:100%;text-align:center;color:var(--white);font-size:33px;font-weight:400}
.quote-mark{position:absolute;top:198px;left:575px}
.quote-frame{position:absolute;top:220px;left:212px;width:782px;height:250px}
.quote-text{position:absolute;top:265px;left:250px;width:700px;text-align:center;color:var(--white);font-size:12px;font-style:italic;line-height:20px}
.quote-name{position:absolute;top:352px;width:100%;text-align:center;color:var(--white);font-size:14px;font-weight:700;font-style:italic}
.quote-dots{position:absolute;top:397px;left:568px;display:flex;gap:4px}
.quote-dots span{width:20px;height:3px;background:rgba(255,255,255,.45)}
.quote-dots span.on{background:var(--white)}

/* Why choose */
.why{position:absolute;top:2620px;left:0;width:1200px;height:445px}
.video{position:absolute;left:120px;top:76px;width:448px;height:282px;border:5px solid #eef1f3;background:linear-gradient(120deg,#f3eee7,#d9d2c8 50%,#b8c3c9)}
.play{position:absolute;left:186px;top:103px;width:70px;height:70px;border-radius:50%;background:var(--white);display:flex;align-items:center;justify-content:center}
.why-copy{position:absolute;left:605px;top:74px;width:470px}
.why-copy h2{font-size:30px;font-weight:400;margin-bottom:22px}
.btn-outline{display:inline-flex;align-items:center;justify-content:center;width:160px;height:44px;margin-top:24px;border:2px solid var(--blue);color:var(--blue);font-weight:700;font-size:15px}

/* Footer */
.site-footer{position:absolute;top:3065px;left:0;width:1200px;height:325px;background:var(--lime);color:var(--white)}
.foot-col{position:absolute;top:58px}
.foot-col h4{font-size:18px;font-weight:400;text-transform:uppercase;margin-bottom:18px}
.foot-col li{list-style:none;font-size:14px;line-height:30px;display:flex;align-items:center;gap:8px;white-space:nowrap}
.socials{display:flex;gap:10px}
.socials span{width:36px;height:36px;border:2px solid var(--white);border-radius:50%}
.footer-bar{position:absolute;top:3390px;left:0;width:1200px;height:72px;background:var(--footer-bar);color:var(--white);font-size:12px;display:flex;align-items:center;justify-content:center}
</style>
</head>
<body>

<header class="site-header">
  <a class="brand" href="#">
    <span class="brand-name">FERNWAY</span>
    <span class="brand-sub">MEDICAL CLINIC</span>
  </a>
  <nav class="main-nav">
    <a href="#">Home</a><a href="#">About Us</a><a class="active" href="#">Services</a><a href="#">Testimonial</a><a href="#">FAQ</a><a href="#">Contact</a>
  </nav>
  <a class="nav-phone" href="#">
    <svg width="20" height="20" viewBox="0 0 24 24"><path fill="#0592cd" d="M6.6 10.8a15.1 15.1 0 0 0 6.6 6.6l2.2-2.2c.3-.3.7-.4 1-.2 1.1.4 2.3.6 3.6.6.6 0 1 .4 1 1V20c0 .6-.4 1-1 1A17 17 0 0 1 3 4c0-.6.4-1 1-1h3.5c.6 0 1 .4 1 1 0 1.3.2 2.5.6 3.6.1.3 0 .7-.2 1z"/></svg>
    (512) 555 0182
  </a>
</header>

<section class="hero">
  <div class="hero-photo" role="img" aria-label="Woman stretching outdoors on green grass"></div>
  <h1 class="hero-title">A HEALTHY LIFESTYLE</h1>
  <a class="btn-ghost" href="#">Schedule an Appointment</a>
  <div class="slider-dots"><span class="on"></span><span></span><span class="on"></span><span></span></div>
</section>

<nav class="mega-menu">
  <div class="mega-col"><h4>Service Heading</h4><ul><li>Morbi diam mauris</li><li>Aliverra in gravida eu</li><li>Cras id elit Integer quis</li><li>Arna Ut ante enim</li></ul></div>
  <div class="mega-col"><h4>Service Heading</h4><ul><li>Lorem ipsum</li><li>Dolor sit amet</li><li>Consectetuer adipiscing</li><li>Elit Nam cursus</li><li>Morbi ut mi</li></ul></div>
  <div class="mega-col"><h4>Service Heading</h4><ul><li>Nullam enim leo</li><li>Morbi diam mauris viverra</li><li>An gravida eu</li><li>Pattis in ante Mo</li></ul></div>
  <div class="mega-col"><h4>Service Heading</h4><ul><li>Curabitur vel dolor</li><li>Ultrices ipsum dictum</li><li>Tristique Praesent</li><li>Vitae lacus Ut velit enim</li></ul></div>
</nav>

<section class="welcome">
  <svg width="1200" height="477" viewBox="0 0 1200 477">
    <defs><linearGradient id="sky" x1="0" y1="0" x2="1" y2="1"><stop offset="0" stop-color="#cfe6f7"/><stop offset=".5" stop-color="#7fb8e2"/><stop offset="1" stop-color="#3f8fc9"/></linearGradient></defs>
    <path role="img" aria-label="Smiling woman stretching under a blue sky" d="M676 0 Q770 300 470 477 L1200 477 L1200 0 Z" fill="url(#sky)"/>
    <path d="M672 0 Q766 300 466 477" fill="none" stroke="#9bcb3c" stroke-width="9"/>
  </svg>
  <div class="welcome-copy">
    <h2>Welcome to Fernway Medical Clinic</h2>
    <p class="lead">Vivamus porttitor purus nisi eleifend libero a tempus libero lectus feugiat felis Morbi diam mauris viverra</p>
    <p class="body-text">ligula pulvinar metus eget consectetuer augue nisi quis lacus Ut ac mi quis lacus mollis aliquam Curabitur iaculis tempus eros Curabitur vel mi sit amet magna malesuada ultrices Ut nisi erat fermentum vel congue id euismod in elit Fusce ultricies orci ac</p>
    <a class="btn-solid" href="#">Learn More</a>
  </div>
</section>

<section class="expect">
  <h2>What to Expect</h2>
  <div class="accordion">
    <div class="acc-open-head">Nam cursus Morbi ut mi Nullam enim leo egestas ?
      <svg width="16" height="10" viewBox="0 0 16 10"><path d="M1 9l7-7 7 7" fill="none" stroke="#0592cd" stroke-width="2"/></svg></div>
    <div class="acc-body">Mauris vel lacus vitae felis vestibulum volutpat Etiam est nunc venenatis in tristique eu imperdiet ac nisl Cum sociis natoque penatibus et magnis dis parturient montes nascetur ridiculus mus In iaculis facilisis massa Etiam eu urna Sed porta Suspendisse quam leo molestie sed</div>
    <div class="acc-item">Mauris vel lacus vitae felis vestibulum volutpat ?<svg width="16" height="10" viewBox="0 0 16 10"><path d="M1 1l7 7 7-7" fill="none" stroke="#fff" stroke-width="2"/></svg></div>
    <div class="acc-item">Vivamus porttitor purus nisi eleifend libero a tempus libero lectus feugiat felis ?<svg width="16" height="10" viewBox="0 0 16 10"><path d="M1 1l7 7 7-7" fill="none" stroke="#fff" stroke-width="2"/></svg></div>
    <div class="acc-item">Ut velit enim vestibulum non fermentum ?<svg width="16" height="10" viewBox="0 0 16 10"><path d="M1 1l7 7 7-7" fill="none" stroke="#fff" stroke-width="2"/></svg></div>
    <div class="acc-item">Aenean porttitor eros vel dolor Donec convallis pede ?<svg width="16" height="10" viewBox="0 0 16 10"><path d="M1 1l7 7 7-7" fill="none" stroke="#fff" stroke-width="2"/></svg></div>
  </div>
</section>

<section class="blogs">
  <h2>Latest Blogs</h2>
  <article class="blog-card" style="left:125px">
    <div class="blog-photo" role="img" aria-label="Patient receiving a back treatment"></div>
    <div class="blog-date"><b>02</b><small>AUG</small></div>
    <div class="blog-text"><h3>Your Blog Tittle here</h3><p>Gentle stretches each morning help ease joint stiffness and keep your back strong through a busy working day.</p><a class="read-more" href="#">READ MORE</a></div>
  </article>
  <article class="blog-card" style="left:448px">
    <div class="blog-photo" role="img" aria-label="Woman relaxing in a green park"></div>
    <div class="blog-date"><b>02</b><small>AUG</small></div>
    <div class="blog-text"><h3>Your Blog Tittle here</h3><p>Fresh air and a short walk outdoors can lift your mood, lower stress and support better sleep at night.</p><a class="read-more" href="#">READ MORE</a></div>
  </article>
  <article class="blog-card" style="left:776px">
    <div class="blog-photo" role="img" aria-label="Therapist treating a patient's leg"></div>
    <div class="blog-date"><b>02</b><small>AUG</small></div>
    <div class="blog-text"><h3>Your Blog Tittle here</h3><p>Learn what to expect at your first therapy visit, from the initial check to a plan made just for you.</p><a class="read-more" href="#">READ MORE</a></div>
  </article>
</section>

<section class="testimonials" role="img" aria-label="Patient resting during a physiotherapy session">
  <svg class="wave" width="1200" height="60" viewBox="0 0 1200 60"><path d="M0 0 H1200 V10 Q600 70 0 10 Z" fill="#fff"/></svg>
  <h2>Testimonials</h2>
  <svg class="quote-mark" width="50" height="44" viewBox="0 0 50 44"><path fill="#fff" d="M4 4h18v18c0 10-6 18-16 20l-2-5c6-2 9-6 9-11H4zM28 4h18v18c0 10-6 18-16 20l-2-5c6-2 9-6 9-11h-9z"/></svg>
  <svg class="quote-frame" width="782" height="250" viewBox="0 0 782 250"><path d="M2 62V2h60M780 188v60h-60" fill="none" stroke="#fff" stroke-width="3"/></svg>
  <p class="quote-text">“ The whole team made me feel welcome from my very first visit. After a few weeks of care my back pain eased and I was able to return to running, hiking and playing with my kids. I tell every friend about this friendly, caring clinic and its staff.</p>
  <p class="quote-name">Dana Reyes - Prairie Hollow Savings</p>
  <div class="quote-dots"><span class="on"></span><span></span><span></span></div>
</section>

<section class="why">
  <div class="video" role="img" aria-label="Therapist massaging a patient's leg, video preview">
    <span class="play"><svg width="22" height="26" viewBox="0 0 22 26"><path d="M2 1l19 12L2 25z" fill="#111"/></svg></span>
  </div>
  <div class="why-copy">
    <h2>Why Choose Us</h2>
    <p class="lead">Vivamus porttitor purus nisi eleifend libero a tempus libero lectus feugiat felis Morbi diam mauris viverra</p>
    <p class="body-text">ligula pulvinar metus eget consectetuer augue nisi quis lacus Ut ac mi quis lacus mollis aliquam Curabitur iaculis tempus eros Curabitur vel mi sit amet magna malesuada ultrices</p>
    <a class="btn-outline" href="#">Learn More</a>
  </div>
</section>

<footer class="site-footer">
  <div class="foot-col" style="left:122px"><h4>Quick Links</h4><ul><li>Home</li><li>About Us</li><li>Why Us</li><li>What to expect</li></ul></div>
  <div class="foot-col" style="left:347px"><h4>Resources</h4><ul><li>Our Services</li><li>Testimonials</li><li>Our Blogs</li><li>Contact Us</li></ul></div>
  <div class="foot-col" style="left:560px"><h4>Contact Info</h4><ul>
    <li><svg width="14" height="16" viewBox="0 0 14 18"><path d="M7 1a6 6 0 0 1 6 6c0 4-6 10-6 10S1 11 1 7a6 6 0 0 1 6-6z" fill="none" stroke="#fff" stroke-width="2"/><circle cx="7" cy="7" r="2" fill="#fff"/></svg>248 Linden Row Suite 4 Austin TX 78701</li>
    <li><svg width="14" height="14" viewBox="0 0 24 24"><path fill="#fff" d="M6.6 10.8a15.1 15.1 0 0 0 6.6 6.6l2.2-2.2c.3-.3.7-.4 1-.2 1.1.4 2.3.6 3.6.6.6 0 1 .4 1 1V20c0 .6-.4 1-1 1A17 17 0 0 1 3 4c0-.6.4-1 1-1h3.5c.6 0 1 .4 1 1 0 1.3.2 2.5.6 3.6.1.3 0 .7-.2 1z"/></svg>512.555.0147</li>
    <li><svg width="16" height="12" viewBox="0 0 16 12"><rect x="1" y="1" width="14" height="10" fill="none" stroke="#fff" stroke-width="1.5"/><path d="M1 1l7 6 7-6" fill="none" stroke="#fff" stroke-width="1.5"/></svg>hello@fernwayclinic.com</li>
  </ul></div>
  <div class="foot-col" style="left:903px"><h4>Follow Us</h4><div class="socials"><span></span><span></span><span></span><span></span></div></div>
</footer>
<div class="footer-bar">© 2017 Fernway Medical Clinic. All right reserved. Terms of Use</div>

</body>
</html>
```